Corvane Capital Business Cards

These are professional business cards that are for my family office.
Put fake emails and phone numbers as of now until I finalize those components. This family office controls my families investments, assets, and future. The cards should be professional.
..
.
.
.
I just uploaded another variation of a logo I would like to see as a business card to I am inbeteen which logo to use

Target Market(s)

business

Industry/Entity Type

business

Contact Information for Business Card

Professional, wealth related, finance related.

Requirements
Must have
• Logo

```html
<!DOCTYPE html>
<html lang="en">
<head>
<meta charset="utf-8">
<title>Corvane Capital — Business Cards</title>
<link rel="stylesheet" href="https://fonts.googleapis.com/css2?family=Playfair+Display:wght@400;700&family=Tinos&display=swap">
<style>
  :root {
    --backdrop: #e6e6e6;
    --gold: #c8ae71;
    --ink: #231f20;
    --paper: #ffffff;
    --ghost: #f1f1f1;
  }
  * { box-sizing: border-box; margin: 0; padding: 0; }
  html, body { width: 1200px; height: 1200px; overflow: hidden; }
  body { background: var(--backdrop); position: relative; font-family: "Tinos", serif; color: var(--ink); }

  .card { position: absolute; left: 286px; width: 628px; height: 359px; border-radius: 17px; overflow: hidden; }
  .card-front { top: 230px; background: var(--gold); }
  .card-back { top: 610px; background: var(--paper); }

  .brand-plate {
    position: absolute; left: 143px; top: 125px; width: 342px; height: 109px;
    background: var(--paper); border: 2px solid var(--ink); border-radius: 22px;
    display: flex; align-items: center; justify-content: center; gap: 10px;
  }
  .brand-mark { width: 14px; height: 14px; background: var(--ink); flex: none; }
  .brand-name { font-family: "Playfair Display", serif; font-weight: 400; font-size: 25px; letter-spacing: 0.5px; color: var(--ink); white-space: nowrap; }

  .ghost-name {
    position: absolute; left: 79px; top: 204px; font-family: "Playfair Display", serif;
    font-size: 59px; line-height: 1; color: var(--ghost); white-space: nowrap;
  }

  .holder-name { position: absolute; left: 47px; top: 52px; font-family: "Playfair Display", serif; font-weight: 700; font-size: 19px; line-height: 1; }
  .holder-name .surname { color: var(--gold); }
  .holder-role { position: absolute; left: 47px; top: 75px; font-size: 14px; color: var(--gold); line-height: 1; }

  .rule { position: absolute; background: var(--gold); }
  .rule-v { width: 1px; }
  .rule-h { height: 1px; }

  .contact-row { position: absolute; left: 79px; font-size: 15px; line-height: 1; white-space: nowrap; }
  .contact-icon { position: absolute; left: 56px; width: 14px; height: 14px; }

  .address { position: absolute; left: 266px; top: 153px; font-size: 15px; line-height: 19px; }
  .address-icon { position: absolute; left: 233px; top: 170px; width: 21px; height: 21px; }

  .corner-brand { position: absolute; right: 46px; top: 276px; display: flex; align-items: center; gap: 9px; }
  .corner-brand .brand-name { font-size: 22px; }
  .corner-brand .brand-mark { width: 12px; height: 12px; }

  .band { position: absolute; left: 0; top: 314px; width: 628px; height: 23px; }
</style>
</head>
<body>
  <section class="card card-front" aria-label="Card front">
    <div class="brand-plate">
      <span class="brand-mark"></span>
      <span class="brand-name">CORVANE CAPITAL</span>
    </div>
  </section>

  <section class="card card-back" aria-label="Card back">
    <div class="ghost-name" aria-hidden="true">CORVANE CAPITAL</div>

    <div class="holder-name">Elias <span class="surname">Marlow</span></div>
    <div class="holder-role">Desingner</div>

    <div class="rule rule-v" style="left:74px; top:135px; height:93px;"></div>
    <div class="rule rule-h" style="left:50px; top:168px; width:143px;"></div>
    <div class="rule rule-h" style="left:50px; top:188px; width:143px;"></div>
    <div class="rule rule-h" style="left:50px; top:207px; width:143px;"></div>

    <svg class="contact-icon" style="top:152px" viewBox="0 0 24 24" aria-hidden="true"><path d="M6.6 10.8c1.4 2.8 3.8 5.1 6.6 6.6l2.2-2.2c.3-.3.7-.4 1-.2 1.1.4 2.3.6 3.6.6.6 0 1 .4 1 1V20c0 .6-.4 1-1 1C10.6 21 3 13.4 3 4c0-.6.4-1 1-1h3.5c.6 0 1 .4 1 1 0 1.3.2 2.5.6 3.6.1.3 0 .7-.2 1z" fill="none" stroke="#231f20" stroke-width="2"/><path d="M14 3a7 7 0 0 1 7 7M14 7a3 3 0 0 1 3 3" fill="none" stroke="#231f20" stroke-width="2"/></svg>
    <div class="contact-row" style="top:152px">0145 0145 0145</div>

    <svg class="contact-icon" style="top:172px" viewBox="0 0 24 24" aria-hidden="true"><rect x="3" y="6" width="18" height="12" fill="none" stroke="#231f20" stroke-width="2"/><path d="M3 6l9 7 9-7" fill="none" stroke="#231f20" stroke-width="2"/></svg>
    <div class="contact-row" style="top:172px">hello@corvanecap.com</div>

    <svg class="contact-icon" style="top:191px" viewBox="0 0 24 24" aria-hidden="true"><circle cx="12" cy="12" r="9" fill="none" stroke="#231f20" stroke-width="2"/><ellipse cx="12" cy="12" rx="4" ry="9" fill="none" stroke="#231f20" stroke-width="2"/><path d="M3 12h18" stroke="#231f20" stroke-width="2"/></svg>
    <div class="contact-row" style="top:191px">www.corvanecap.com</div>

    <div class="rule rule-v" style="left:227px; top:135px; height:93px;"></div>
    <div class="rule rule-h" style="left:227px; top:148px; width:129px;"></div>
    <div class="rule rule-h" style="left:227px; top:219px; width:129px;"></div>

    <svg class="address-icon" viewBox="0 0 24 24" aria-hidden="true"><path d="M2 12L12 3l10 9" fill="none" stroke="#231f20" stroke-width="2.4"/><path d="M5 10v11h14V10" fill="none" stroke="#231f20" stroke-width="2.4"/><rect x="10" y="14" width="4" height="7" fill="#231f20"/></svg>
    <address class="address" style="font-style:normal">Your location,<br>Harbor Row,<br>Easton, 100.</address>

    <div class="corner-brand">
      <span class="brand-mark"></span>
      <span class="brand-name">CORVANE CAPITAL</span>
    </div>

    <svg class="band" viewBox="0 0 628 23" aria-hidden="true">
      <polygon points="0,0 410,0 419,23 0,23" fill="#231f20"/>
      <polygon points="449,0 628,0 628,23 458,23" fill="#c8ae71"/>
    </svg>
  </section>
</body>
</html>
```